Powerpoint design template for LUMOTEX for new digital platform

We would like to use a PowerPoint template, we would like to create a new page, we would like to create a new digital platform LUMOTEX for schools and parents for the creation of playful communication and educational tools for children to enhance their positive development, amaze them learn in a playful way. This platform is going to be the most creative, stimulating and innovative classroom, easy to use and fast to implement. Scrapbooking, collages ... Magazine, newsletters Diplomla / awards Slideshows Facebook Calendars Organizers Greetings Games ... This powerpoint template will be used essential to We are looking for a professional design, positioning our brand in the children market with an adult hearing. so you will need to find a good deal. Primary target: nurseries & schools from 0 to 18 years old and universities (in 2nd phase) Secondary target: small & medium businesses Third target: general public, and TPE If it is a color scheme, then it is suggested that it be marketed in Europe (UK, Italy, Spain) and in a 2nd Stage USA and other countries. multiple options for front page, insidious pages (multiple styles with limited text and extended text) and final contact page We need something to read, we can not do it too much, but we can not do it. , and inside pages aligned to our logo

Target Market(s)

Target 1; Education with teacher Target 2; parents and grandparents

Industry/Entity Type

Education

Font styles to use
Other font styles liked:
• not decided. but not too fancy

Requirements
Must have
• Multi page options for front page, page insides (multiple styles with limited text and extended text) and final page contact
Nice to have
• do not have a lot of ideas. We need something to read, we can not get away from it
Should not have
• not too fancy and busy: keep clarity & simplicity while reassuring on quality

```html
<!DOCTYPE html>
<html lang="en">
<head>
<meta charset="utf-8">
<title>LUMOTEX – Inside Page</title>
<link rel="stylesheet" href="https://fonts.googleapis.com/css2?family=Roboto+Condensed:wght@400;700&display=swap">
<style>
  :root {
    --lime: #d9e143;
    --leaf: #8cc63f;
    --orange: #f7941d;
    --ink: #231f20;
    --paper: #fdfdfb;
    --sheen: #ecece6;
    --star-a: #f7941d;
    --star-b: #e0559b;
  }
  * { margin: 0; padding: 0; box-sizing: border-box; }
  html, body { width: 1200px; height: 900px; overflow: hidden; background: var(--paper); }
  .page {
    position: relative;
    width: 1200px;
    height: 900px;
    overflow: hidden;
    background: var(--paper);
    font-family: "Roboto Condensed", "Arial Narrow", sans-serif;
    color: var(--ink);
  }
  .frame { position: absolute; left: 0; top: 0; width: 1200px; height: 900px; }
  .page-title {
    position: absolute;
    left: 27px;
    top: 22px;
    font-size: 46px;
    font-weight: 700;
    line-height: 60px;
    letter-spacing: 0.2px;
  }
  .brand {
    position: absolute;
    right: 44px;
    top: 36px;
    display: flex;
    align-items: center;
    gap: 12px;
  }
  .brand-mark { width: 22px; height: 22px; background: var(--lime); }
  .brand-name { font-size: 40px; font-weight: 700; color: var(--ink); line-height: 1; }
  .section {
    position: absolute;
    left: 30px;
    width: 1100px;
  }
  .section-icon {
    position: absolute;
    left: 0;
    top: 0;
    width: 54px;
    height: 74px;
    border-radius: 6px;
    background: linear-gradient(160deg, var(--star-b), var(--star-a) 55%, var(--lime));
    opacity: 0.85;
  }
  .section-heading {
    position: absolute;
    left: 80px;
    top: 10px;
    font-size: 31px;
    font-weight: 700;
    color: var(--orange);
    line-height: 40px;
  }
  .section-body {
    position: absolute;
    left: 82px;
    top: 54px;
    width: 990px;
    font-size: 22.5px;
    line-height: 36px;
  }
  .section-body .line {
    display: block;
    text-align: justify;
    text-align-last: justify;
    white-space: nowrap;
  }
  .section-body .line.last { text-align-last: left; }
  .site {
    position: absolute;
    left: 21px;
    top: 842px;
    font-size: 24px;
    line-height: 32px;
  }
  .page-number {
    position: absolute;
    right: 21px;
    top: 840px;
    font-size: 24px;
    line-height: 32px;
  }
</style>
</head>
<body>
<div class="page">
  <svg class="frame" viewBox="0 0 1200 900" aria-hidden="true">
    <defs>
      <linearGradient id="sheen" x1="0" y1="0" x2="1" y2="1">
        <stop offset="0" stop-color="#ffffff" stop-opacity="0"/>
        <stop offset="0.5" stop-color="#ecece6" stop-opacity="0.7"/>
        <stop offset="1" stop-color="#ffffff" stop-opacity="0"/>
      </linearGradient>
    </defs>
    <polygon points="760,102 900,102 450,815 330,815" fill="url(#sheen)"/>
    <polygon points="960,0 1010,0 560,815 500,815" fill="url(#sheen)" opacity="0.5"/>
    <polygon points="920,0 968,0 914,106 866,106" fill="var(--leaf)"/>
    <polygon points="0,0 955,0 900,96 0,96" fill="var(--lime)"/>
    <polygon points="0,96 900,96 895,106 0,106" fill="var(--leaf)"/>
    <polygon points="0,815 412,815 388,900 0,900" fill="var(--lime)"/>
    <polygon points="412,815 426,815 402,900 388,900" fill="var(--leaf)"/>
    <polygon points="436,815 1200,815 1200,900 386,900" fill="var(--orange)"/>
    <polygon points="426,815 436,815 412,900 402,900" fill="#ffffff"/>
  </svg>

  <h1 class="page-title">PROJECT TITLE HERE</h1>

  <div class="brand">
    <span class="brand-mark"></span>
    <span class="brand-name">LUMOTEX</span>
  </div>

  <section class="section" style="top:168px">
    <div class="section-icon" role="img" aria-label="Colourful shooting-star illustration"></div>
    <h2 class="section-heading">SUBTEXT HERE</h2>
    <p class="section-body">
      <span class="line">Toffee caramels candy canes bonbon bonbon soufflé bonbon wafer. Topping I love halvah I love. Jujubes</span>
      <span class="line">lemon drops I love jelly pie chocolate bar. Biscuit oat cake carrot cake. Muffin jelly beans chocolate choco-</span>
      <span class="line last">late. Sugar plum I love cheesecake marshmallow cocoa cake sweet cookies topping jelly gummies.</span>
    </p>
  </section>

  <section class="section" style="top:364px">
    <div class="section-icon" role="img" aria-label="Colourful shooting-star illustration"></div>
    <h2 class="section-heading">SUBTEXT HERE</h2>
    <p class="section-body">
      <span class="line">Toffee caramels candy canes bonbon bonbon soufflé bonbon wafer. Topping I love halvah I love. Jujubes</span>
      <span class="line">lemon drops I love jelly pie chocolate bar. Biscuit oat cake carrot cake. Muffin jelly beans chocolate choco-</span>
      <span class="line last">late. Sugar plum I love cheesecake marshmallow cocoa cake sweet cookies topping jelly gummies.</span>
    </p>
  </section>

  <section class="section" style="top:600px">
    <div class="section-icon" role="img" aria-label="Colourful shooting-star illustration"></div>
    <h2 class="section-heading">SUBTEXT HERE</h2>
    <p class="section-body">
      <span class="line">Toffee caramels candy canes bonbon bonbon soufflé bonbon wafer. Topping I love halvah I love. Jujubes</span>
      <span class="line">lemon drops I love jelly pie chocolate bar. Biscuit oat cake carrot cake. Muffin jelly beans chocolate choco-</span>
      <span class="line last">late. Sugar plum I love cheesecake marshmallow cocoa cake sweet cookies topping jelly gummies.</span>
    </p>
  </section>

  <div class="site">www.lumotex.com</div>
  <div class="page-number">Page : 01</div>
</div>
</body>
</html>
```